Brewlark Cup Society - A Monthly Subscription Coffee Club - Shopify Website Design

A monthly subscription company. Need a Shopify Website Design and uploaded to fully work with Tidal Renewals.

Please look at these sites for examples as well as the images I enclosed.

https://www.sipvantor.com/
https://mokrate.com/
https://www.platewinder.com/
https://www.globunchies.com/

Number of Pages Required

1 page

```html
<!DOCTYPE html>
<html lang="en">
<head>
<meta charset="utf-8">
<title>Brewlark Cup Society</title>
<link href="https://fonts.googleapis.com/css2?family=Lato:wght@400;700;900&family=Pacifico&display=swap" rel="stylesheet">
<style>
:root{
  --accent:#f4a53c;
  --ink:#1f1f1f;
  --muted:#8a8a8a;
  --line:#e6e6e6;
  --white:#ffffff;
  --dark:#2a1c14;
}
*{margin:0;padding:0;box-sizing:border-box}
html,body{width:1200px;height:3636px;overflow:hidden;background:var(--white);font-family:'Lato',sans-serif;color:var(--ink)}
.page{position:relative;width:1200px;height:3636px}
.abs{position:absolute}
.script{font-family:'Pacifico',cursive;font-weight:400}
.btn{display:inline-flex;align-items:center;gap:10px;background:var(--accent);color:var(--white);font-size:14px;font-weight:700;letter-spacing:1px;padding:0 22px;height:50px;text-transform:uppercase}
.btn .dot{width:14px;height:14px;border-radius:50%;background:var(--white);position:relative}
.btn .dot::after{content:"";position:absolute;left:5px;top:4px;border-left:5px solid var(--accent);border-top:3px solid transparent;border-bottom:3px solid transparent}

/* header */
.site-header{left:0;top:0;width:1200px;height:80px;background:var(--white);display:flex;align-items:center;padding:0 112px}
.brand{display:flex;align-items:center;gap:10px;font-weight:900;font-size:22px;color:var(--accent)}
.brand .mark{width:44px;height:44px;border-radius:50%;background:var(--accent)}
.main-nav{display:flex;gap:30px;margin-left:auto;margin-right:auto;font-size:14px;font-weight:700;text-transform:uppercase}
.main-nav a{color:var(--ink);text-decoration:none}
.main-nav a.active{color:var(--accent)}
.header-tools{display:flex;gap:18px}

/* hero */
.hero{left:0;top:80px;width:1200px;height:500px;background:linear-gradient(135deg,#8e7966 0%,#5a4434 40%,#7a6656 70%,#c9bcae 100%)}
.hero-title{left:0;top:220px;width:1200px;text-align:center;color:var(--white);font-size:62px}
.hero .btn{position:absolute;left:528px;top:330px}

/* about */
.about-photo{left:112px;top:688px;width:468px;height:360px;background:linear-gradient(135deg,#8a5a35,#4a2c18 55,#caa886)}
.about-photo{background:linear-gradient(135deg,#8a5a35 0%,#4a2c18 55%,#caa886 100%)}
.about-title{left:672px;top:700px;font-size:46px}
.about-text{left:672px;top:780px;width:420px;font-size:14px;line-height:24px;color:var(--muted)}
.about .btn{position:absolute;left:672px;top:955px}

/* feature cards */
.feature{width:316px}
.feature .photo{width:316px;height:208px}
.feature h3{margin-top:24px;font-size:15px;font-weight:900;text-transform:uppercase}
.feature p{margin-top:8px;font-size:13px;line-height:21px;color:var(--muted);padding-right:30px}

/* products */
.section-title{left:0;width:1200px;text-align:center;font-size:40px}
.product{width:236px}
.product .frame{width:236px;height:212px;border:1px solid var(--line);display:flex;align-items:center;justify-content:center}
.product .thumb{width:150px;height:110px;background:linear-gradient(135deg,#b98b5c,#5b3a22)}
.product h4{margin-top:22px;font-size:17px;font-weight:900;text-transform:uppercase}
.product .price{margin-top:6px;font-size:20px}

/* banner */
.banner{left:0;top:2040px;width:1200px;height:440px;background:linear-gradient(180deg,#3a2a20 0%,#1e140e 50%,#5a4230 100%)}
.banner h2{position:absolute;left:0;top:160px;width:1200px;text-align:center;color:var(--white);font-size:40px}
.banner p{position:absolute;left:0;top:250px;width:1200px;text-align:center;color:var(--white);font-size:16px;font-weight:700}

/* testimonials */
.quote{width:300px}
.quote .mark{font-family:Georgia,serif;font-size:44px;line-height:30px;color:var(--accent);font-weight:700}
.quote p{margin-top:14px;font-size:13px;line-height:23px;color:var(--muted);text-align:justify}
.quote .name{margin-top:20px;font-size:13px;font-weight:900;text-transform:uppercase}

/* gallery */
.gallery{left:0;top:2868px;width:1200px;height:372px;display:flex}
.gallery div{flex:1}

/* footer */
.footer-head{font-size:14px;font-weight:900;text-transform:uppercase}
.footer-links{display:flex;gap:24px;font-size:13px;font-weight:700;text-transform:uppercase}
.newsletter{left:672px;top:3358px;display:flex}
.newsletter .field{width:290px;height:50px;border:1px solid var(--line);border-right:none;font-size:13px;color:var(--muted);padding:0 18px;display:flex;align-items:center}
.newsletter .submit{width:124px;height:50px;background:var(--accent);color:var(--white);font-size:13px;font-weight:900;display:flex;align-items:center;justify-content:center;text-transform:uppercase}
.footer-rule{left:112px;top:3470px;width:976px;height:1px;background:var(--line)}
.currency{left:112px;top:3508px;width:80px;height:34px;border:1px solid var(--line);font-size:13px;font-weight:700;display:flex;align-items:center;justify-content:space-between;padding:0 10px}
.pay{display:flex;gap:8px}
.pay span{width:40px;height:24px;border:1px solid var(--line);border-radius:3px;background:#f4f4f4}
.social{display:flex;gap:18px}
.social span{width:22px;height:22px;border-radius:50%;background:var(--accent)}
.copyright{left:788px;top:3572px;width:300px;text-align:right;font-size:12px;color:var(--muted)}
</style>
</head>
<body>
<div class="page">

  <header class="site-header abs">
    <div class="brand"><span class="mark"></span>Brewlark Cup Society</div>
    <nav class="main-nav">
      <a class="active">Home</a><a>About Us</a><a>Our Products</a><a>Latest Blog</a><a>Contact Us</a>
    </nav>
    <div class="header-tools">
      <svg width="18" height="18" viewBox="0 0 18 18"><circle cx="7.5" cy="7.5" r="5.5" fill="none" stroke="#f4a53c" stroke-width="2"/><line x1="11.5" y1="11.5" x2="16" y2="16" stroke="#f4a53c" stroke-width="2"/></svg>
      <svg width="20" height="18" viewBox="0 0 20 18"><path d="M1 2h3l2 10h11l2-7H6" fill="none" stroke="#f4a53c" stroke-width="2"/><circle cx="8" cy="16" r="1.6" fill="#f4a53c"/><circle cx="15" cy="16" r="1.6" fill="#f4a53c"/></svg>
    </div>
  </header>

  <section class="hero abs" role="img" aria-label="Wooden box of roasted coffee beans on a woven mat">
    <h1 class="hero-title abs script">Brewlark Cup Society</h1>
    <span class="btn">Get Started <span class="dot"></span></span>
  </section>

  <section class="about">
    <div class="about-photo abs" role="img" aria-label="Cup of coffee beside a wooden tray of beans and sugar cubes"></div>
    <h2 class="about-title abs script">About Us</h2>
    <p class="about-text abs">Sed ut perspiciatis unde omnis iste natus error sit voluptatem accusantium doloremque laudantium, totam rem aperiam, eaque ipsa quae ab illo inventore veritatis et quasi architecto beatae vitae dicta sunt explicabo. Nemo enim ipsam voluptatem quia voluptas sit aspernatur aut odit aut fugit sed quia consequuntur magni dolores eos qui ratione voluptatem.</p>
    <span class="btn">Read More <span class="dot"></span></span>
  </section>

  <article class="feature abs" style="left:112px;top:1152px">
    <div class="photo" role="img" aria-label="Coffee grinder and beans on a dark table" style="background:linear-gradient(135deg,#5a4130,#2a1d14)"></div>
    <h3>Comparison</h3>
    <p>At vero eos et accusamus et iusto odio dignissimos ducimus qui blanditiis praesentium voluptatum deleniti atque.</p>
  </article>
  <article class="feature abs" style="left:440px;top:1152px">
    <div class="photo" role="img" aria-label="Hands holding a wooden box filled with coffee beans" style="background:linear-gradient(135deg,#7a5a3e,#3a271a)"></div>
    <h3>Rounding Box</h3>
    <p>At vero eos et accusamus et iusto odio dignissimos ducimus qui blanditiis praesentium voluptatum deleniti atque.</p>
  </article>
  <article class="feature abs" style="left:768px;top:1152px">
    <div class="photo" role="img" aria-label="Scoop of coffee beans on a dark surface" style="background:linear-gradient(135deg,#3a2c22,#6b5140)"></div>
    <h3>Categorization</h3>
    <p>At vero eos et accusamus et iusto odio dignissimos ducimus qui blanditiis praesentium voluptatum deleniti atque.</p>
  </article>

  <h2 class="section-title abs script" style="top:1560px">Featured Products</h2>
  <div class="product abs" style="left:96px;top:1668px"><div class="frame"><div class="thumb" role="img" aria-label="Wooden crate of coffee beans"></div></div><h4>Product Title</h4><div class="price">$500.00</div></div>
  <div class="product abs" style="left:352px;top:1668px"><div class="frame"><div class="thumb" role="img" aria-label="Divided box of coffee varieties"></div></div><h4>Product Title</h4><div class="price">$500.00</div></div>
  <div class="product abs" style="left:608px;top:1668px"><div class="frame"><div class="thumb" role="img" aria-label="Small box of ground coffee"></div></div><h4>Product Title</h4><div class="price">$500.00</div></div>
  <div class="product abs" style="left:864px;top:1668px"><div class="frame"><div class="thumb" role="img" aria-label="Manual coffee grinder with beans"></div></div><h4>Product Title</h4><div class="price">$500.00</div></div>

  <section class="banner abs" role="img" aria-label="Dark close-up of roasted coffee beans">
    <h2 class="script">Looking for our enterprise security offerings</h2>
    <p>Lorem ipsum dolor sit amet, consectetur adipiscing elit, sed do eiusmod tempor</p>
  </section>

  <div class="quote abs" style="left:112px;top:2556px"><div class="mark">“</div><p>Sed ut perspiciatis unde omnis iste natus error sit voluptatem accusantium doloremque laudantium, totam rem aperiam, eaque ipsa quae ab illo inventore veritatis et quasi architecto beatae vitae dicta sunt.</p><div class="name">Rackham</div></div>
  <div class="quote abs" style="left:448px;top:2556px"><div class="mark">“</div><p>Sed ut perspiciatis unde omnis iste natus error sit voluptatem accusantium doloremque laudantium, totam rem aperiam, eaque ipsa quae ab illo inventore veritatis et quasi architecto beatae vitae dicta sunt.</p><div class="name">Rackham</div></div>
  <div class="quote abs" style="left:784px;top:2556px"><div class="mark">“</div><p>Sed ut perspiciatis unde omnis iste natus error sit voluptatem accusantium doloremque laudantium, totam rem aperiam, eaque ipsa quae ab illo inventore veritatis et quasi architecto beatae vitae dicta sunt.</p><div class="name">Rackham</div></div>

  <section class="gallery abs">
    <div role="img" aria-label="Hand opening a wooden coffee box" style="background:linear-gradient(135deg,#a57a52,#4a3020)"></div>
    <div role="img" aria-label="Stacked wooden boxes spilling coffee beans" style="background:linear-gradient(135deg,#2a1a10,#7a4e2e)"></div>
    <div role="img" aria-label="Open wooden chest with coffee beans" style="background:linear-gradient(135deg,#c9a47e,#5a3820)"></div>
  </section>

  <footer>
    <div class="footer-head abs" style="left:112px;top:3322px">Quick Links</div>
    <nav class="footer-links abs" style="left:112px;top:3374px"><a>Home</a><a>About Us</a><a>Our Products</a><a>Latest Blog</a><a>Contact Us</a></nav>
    <div class="footer-head abs" style="left:672px;top:3322px">Newsletter</div>
    <div class="newsletter abs"><div class="field">Email Address</div><div class="submit">Subscribe</div></div>
    <div class="footer-rule abs"></div>
    <div class="currency abs">USD $ <svg width="10" height="6" viewBox="0 0 10 6"><path d="M1 1l4 4 4-4" fill="none" stroke="#1f1f1f" stroke-width="1.5"/></svg></div>
    <div class="pay abs" style="left:112px;top:3560px"><span></span><span></span><span></span></div>
    <div class="social abs" style="left:818px;top:3516px"><span></span><span></span><span></span><span></span></div>
    <div class="copyright abs">© 2021 Brewlark Cup Society. All Rights Reserved</div>
  </footer>

</div>
</body>
</html>
```